Report template for evaluation reports to be used by non designers

We are looking for a report template that meets all the requirements listed in the attached documents. letter head, logo etc have been enclosed. Its important that the colour integrity is kept, but beyond that options are welcome.
Its important that the document is extremely easy to use and that is able to be adapted to include eatables, figures, pictures, text boxes etc and keep the integrity of the template

Target Market(s)

Governments, Civil society organisations and research institutions

Font styles to use
Sans Serif

Colors
6b449b
876aae
c0c0c0
000000

Requirements
Must have
• Clean, professional, not concluded, modern, must be easy to use
Should not have
• too busy, hard to use

```html
<!DOCTYPE html>
<html lang="en">
<head>
<meta charset="utf-8">
<title>Quorvane Research Institute – Report 2018 Cover</title>
<link rel="stylesheet" href="https://fonts.googleapis.com/css2?family=Oswald:wght@700&family=Open+Sans:wght@400;600&display=swap">
<style>
  :root {
    --purple-deep: #6b449b;
    --purple-mid: #765ea9;
    --purple-soft: #9e8ac4;
    --silver: #c0c0c0;
    --silver-dark: #9a9a9a;
    --ink: #1f1f1f;
    --paper: #ffffff;
    --backdrop: #dcdcdc;
    --rule: #cfc6e2;
  }
  html, body {
    margin: 0;
    width: 1200px;
    height: 784px;
    overflow: hidden;
    background: var(--backdrop);
  }
  .cover {
    position: absolute;
    left: 340px;
    top: 24px;
    width: 520px;
    height: 736px;
    background: var(--paper);
    box-shadow: 0 10px 30px rgba(0,0,0,0.18);
    overflow: hidden;
  }
  .cover__graphics {
    position: absolute;
    inset: 0;
  }
  .cover__title {
    position: absolute;
    right: 42px;
    top: 58px;
  }
  .cover__title-main {
    font-family: 'Oswald', sans-serif;
    font-weight: 700;
    font-size: 46px;
    line-height: 1;
    letter-spacing: 1px;
    color: var(--purple-deep);
    margin: 0;
  }
  .cover__title-year {
    font-family: 'Open Sans', sans-serif;
    font-weight: 400;
    font-size: 34px;
    letter-spacing: 18px;
    color: var(--silver-dark);
    margin: 4px 0 0;
  }
  .cover__photo-label {
    position: absolute;
    left: 196px;
    top: 262px;
    width: 162px;
    height: 162px;
    display: flex;
    align-items: center;
    justify-content: center;
    font-family: 'Open Sans', sans-serif;
    font-weight: 600;
    font-size: 44px;
    color: var(--paper);
    pointer-events: none;
  }
  .brand {
    position: absolute;
    left: 44px;
    bottom: 48px;
    font-family: 'Open Sans', sans-serif;
    color: var(--ink);
  }
  .brand__name {
    font-weight: 400;
    font-size: 50px;
    letter-spacing: 10px;
    line-height: 1;
    margin: 0;
  }
  .brand__tagline {
    font-weight: 400;
    font-size: 12px;
    letter-spacing: 5px;
    margin: 8px 0 0 4px;
  }
  .cover__band {
    position: absolute;
    left: 0;
    right: 0;
    bottom: 0;
    height: 10px;
    background: var(--purple-mid);
  }
</style>
</head>
<body>
  <main class="cover">
    <svg class="cover__graphics" width="520" height="736" viewBox="0 0 520 736">
      <g class="guide-rules" stroke="var(--rule)" stroke-width="1.2" fill="none">
        <line x1="150" y1="120" x2="150" y2="560"/>
        <line x1="420" y1="250" x2="420" y2="600"/>
        <line x1="50" y1="460" x2="430" y2="460"/>
        <line x1="120" y1="210" x2="300" y2="210"/>
      </g>
      <polygon class="accent-triangle" points="232,78 272,78 252,118" fill="var(--purple-mid)"/>
      <polygon class="accent-triangle__facet" points="252,78 272,78 262,98" fill="var(--purple-soft)"/>
      <rect class="square square--top" x="90" y="150" width="74" height="74" fill="var(--purple-mid)"/>
      <rect class="square square--grey" x="70" y="470" width="66" height="66" fill="var(--silver)"/>
      <rect class="square square--bottom" x="360" y="448" width="92" height="92" fill="var(--purple-mid)"/>
      <g class="photo-frame">
        <rect x="160" y="226" width="117" height="117" fill="var(--purple-deep)"/>
        <rect x="277" y="226" width="117" height="117" fill="var(--purple-soft)"/>
        <rect x="160" y="343" width="117" height="117" fill="var(--purple-soft)"/>
        <rect x="277" y="343" width="117" height="117" fill="var(--purple-mid)"/>
        <rect x="190" y="256" width="174" height="174" fill="var(--paper)"/>
      </g>
      <defs>
        <linearGradient id="photoTone" x1="0" y1="0" x2="1" y2="1">
          <stop offset="0" stop-color="#3a3a40"/>
          <stop offset="0.55" stop-color="#6f7480"/>
          <stop offset="1" stop-color="#c9dbe6"/>
        </linearGradient>
      </defs>
      <rect class="photo" x="196" y="262" width="162" height="162" fill="url(#photoTone)" role="img" aria-label="Cover photograph: tall building facade against the sky"/>
    </svg>

    <div class="cover__photo-label">Image</div>

    <header class="cover__title">
      <h1 class="cover__title-main">REPORT</h1>
      <p class="cover__title-year">2018</p>
    </header>

    <div class="brand">
      <p class="brand__name">QUORVANE</p>
      <p class="brand__tagline">RESEARCH INSTITUTE</p>
    </div>

    <div class="cover__band"></div>
  </main>
</body>
</html>
```